Business cards to launch an education platform

Hi,
I am looking at having new business cards designed.
I am a startup, developing a web platform for schools and university, the education world. It's an online assessment system.
I would like a card that looks classy, and that is using the colors and the font of my logo.

I have attached:
1) my logo
2) A business card that I have designed quickly so you can have all the information required in the card, but I really don't like it.
3) The font that I am using (Lato Regular) to design my web platform
4) Some screenshots of my web platform so you can have a look at the style that I have.

Target Market(s)

Major market: Education system: Schools and university
Minor markets: Business in general

Industry/Entity Type

Business

Contact Information for Business Card

Clara Fenwick
Director

M: 0437 518 902
E: clara.fenwick@amberLoomSystems.com.au

Requirements
Must have
• The colors of my logo

```html
<!DOCTYPE html>
<html lang="en">
<head>
<meta charset="utf-8">
<title>Amber Loom Systems – Business Card</title>
<link rel="stylesheet" href="https://fonts.googleapis.com/css2?family=Lato:wght@400;700&display=swap">
<style>
  :root {
    --stage-top: #262626;
    --stage-bottom: #050505;
    --card-white: #ffffff;
    --navy: #173a6b;
    --sky: #1fa3de;
    --brand-top: #23a4e0;
    --brand-bottom: #0f6fbb;
    --mark-blue: #1b7fc6;
  }
  * { margin: 0; padding: 0; box-sizing: border-box; }
  html, body {
    width: 1200px;
    height: 900px;
    overflow: hidden;
  }
  body {
    position: relative;
    background: linear-gradient(180deg, var(--stage-top) 0%, #141414 55%, var(--stage-bottom) 100%);
    font-family: "Lato", sans-serif;
  }
  .card {
    position: absolute;
    top: 306px;
    width: 440px;
    height: 271px;
    border-radius: 12px;
  }
  .card-front {
    left: 149px;
    background: var(--card-white);
  }
  .card-back {
    left: 608px;
    width: 441px;
    background: linear-gradient(180deg, var(--brand-top) 0%, var(--brand-bottom) 100%);
    display: flex;
    align-items: center;
    justify-content: center;
  }
  .holder-name {
    position: absolute;
    left: 24px;
    top: 24px;
    font-size: 17.5px;
    color: var(--sky);
    font-weight: 400;
  }
  .holder-role {
    position: absolute;
    left: 24px;
    top: 48px;
    font-size: 12.5px;
    color: var(--navy);
  }
  .brand-lockup {
    position: absolute;
    right: 26px;
    top: 86px;
    display: flex;
    align-items: center;
    height: 80px;
  }
  .brand-name {
    text-align: right;
    font-size: 22px;
    line-height: 1.2;
    letter-spacing: 2px;
    color: var(--navy);
    font-weight: 400;
    text-transform: uppercase;
  }
  .brand-divider {
    width: 1.5px;
    height: 80px;
    background: var(--sky);
    margin: 0 12px 0 12px;
  }
  .brand-square {
    width: 60px;
    height: 60px;
    background: var(--mark-blue);
  }
  .contact-list {
    position: absolute;
    left: 24px;
    top: 200px;
    list-style: none;
    font-size: 13px;
    color: var(--navy);
  }
  .contact-list li {
    display: flex;
    align-items: center;
    height: 16px;
  }
  .contact-list svg {
    width: 10px;
    height: 10px;
    margin-right: 6px;
    fill: var(--sky);
  }
  .back-name {
    color: var(--card-white);
    font-size: 30px;
    letter-spacing: 3px;
    text-transform: uppercase;
    text-align: center;
    line-height: 1.25;
    font-weight: 400;
  }
</style>
</head>
<body>
  <section class="card card-front">
    <h1 class="holder-name">Clara Fenwick</h1>
    <p class="holder-role">Director</p>

    <div class="brand-lockup">
      <p class="brand-name">Amber Loom<br>Systems</p>
      <span class="brand-divider"></span>
      <span class="brand-square"></span>
    </div>

    <ul class="contact-list">
      <li>
        <svg viewBox="0 0 10 10" aria-hidden="true"><path d="M2 0.5 L3.6 2.6 L2.7 3.6 Q3.6 5.8 6.4 7.3 L7.4 6.4 L9.5 8 L8.2 9.5 Q4.5 9.2 2.2 6.6 Q0.4 4.4 0.5 1.8 Z"/></svg>
        0437 518 902
      </li>
      <li>
        <svg viewBox="0 0 10 10" aria-hidden="true"><path d="M1 2.5 H9 V8 H1 Z M1.3 2.8 L5 5.6 L8.7 2.8" stroke="#fff" stroke-width="0.7"/></svg>
        clara.fenwick@amberLoomSystems.com.au
      </li>
    </ul>
  </section>

  <section class="card card-back">
    <p class="back-name">Amber Loom<br>Systems</p>
  </section>
</body>
</html>
```